Special Gift Box Design for Torvel Ridge Roasters Vietnam

We need a design for a coffee gift box - the design should reflect the premium quality of our coffee products - it should look elegant, classic, stylish, luxury. We will mostly use the box as a present for our main customers and business partners and sell it in our coffee shops.
The dimensions of the box are 26x10.5x9cm (LxWxH). The Box will contain one bag of coffee (250g) and one Vietnamese coffee filter.
We are a coffee producer in the Central Highlands of Vietnam with a sustainable, fair and inclusive business model. We are producing Arabica coffee from farm to cup. We are sourcing our coffee cherries directly from local farmers which are members of an ethnic minority. Besides Arabica and Specialty Arabicas, we also produce Robusta, blends and herbal coffees with Ginseng and Ganoderma. Our products are sold to 4 and 5-star hotels, in online and retail shops in Vietnam and we will soon start to export our coffee to other countries in Asia and overseas.
We are Greenleaf Accord certified and have received many awards (golden brand of Vietnam, special product from Dalat, typical rural industrial product of Central Vietnam etc.) for our outstanding product quality and our socially responsible business concept. We are a member of the Premium Brew Federation (PBF) and a certified PBF roaster. We are creating stable jobs in a remote and poor area of the Central Highlands.

Have also attached the type of box we will produce with the cover opening on one side

Target Market(s)

For now Vietnam and Thailand, but later also oversea markets, so it should be an international design which can (but no must) have asian/vietnamese elements

Industry/Entity Type

Agriculture, coffee producer

Requirements
Must have
• Our logo must be prominently displayed on the box, otherwise no text or product information will be on the box for now.

```html
<!DOCTYPE html>
<html lang="en">
<head>
<meta charset="utf-8">
<title>Torvel Ridge Roasters – Gift Box Panels</title>
<link href="https://fonts.googleapis.com/css2?family=Teko:wght@500&family=Roboto+Condensed:ital,wght@1,400&display=swap" rel="stylesheet">
<style>
  :root{
    --stage:#e9e9e9;
    --box-black:#141414;
    --box-black-soft:#222222;
    --band-red:#c9372c;
    --band-red-deep:#8e1d16;
    --kraft:#c59a66;
    --kraft-ink:#2a1a10;
    --cream:#f3eec4;
    --accent-rose:#d0575b;
    --pattern-grey:#3a3a3a;
    --pattern-dark:#2b0c08;
  }
  *{margin:0;padding:0;box-sizing:border-box}
  html,body{width:1200px;height:767px;overflow:hidden;background:var(--stage)}
  .canvas{position:relative;width:1200px;height:767px}
  .panel{position:absolute;overflow:hidden}
  .panel-lid{left:40px;top:80px;width:780px;height:315px;background:var(--box-black)}
  .panel-front{left:40px;top:395px;width:780px;height:270px;background:var(--box-black)}
  .panel-end{left:850px;top:395px;width:310px;height:270px;background:var(--kraft)}
  .pattern{position:absolute}
  .lid-pattern-left{left:0;top:0;width:40px;height:100%;background:linear-gradient(90deg,var(--pattern-grey),var(--box-black-soft))}
  .lid-pattern-right{right:0;top:0;width:40px;height:100%;background:linear-gradient(270deg,var(--pattern-grey),var(--box-black-soft))}
  .front-band{position:absolute;left:0;right:0;top:60px;bottom:0;background:var(--band-red)}
  .front-pattern-left{left:0;top:0;width:28px;height:100%;background:var(--pattern-dark)}
  .front-pattern-right{right:0;top:0;width:28px;height:100%;background:var(--pattern-dark)}
  .brand{display:flex;align-items:center;gap:16px;position:absolute;font-family:'Teko',sans-serif;font-weight:500;text-transform:uppercase;line-height:.9}
  .brand-dot{border-radius:50%;flex:none}
  .brand-lid{left:50%;top:50%;transform:translate(-50%,-50%);color:var(--cream);font-size:64px}
  .brand-lid .brand-dot{width:26px;height:26px;background:var(--accent-rose)}
  .brand-front{left:90px;top:50%;transform:translateY(-50%);color:var(--band-red-deep);font-size:58px;width:330px}
  .brand-front .brand-dot{width:24px;height:24px;background:var(--band-red-deep)}
  .brand-end{left:50%;top:50%;transform:translate(-50%,-50%);color:var(--kraft-ink);font-size:40px;width:230px;text-align:center;justify-content:center}
  .brand-end .brand-dot{width:18px;height:18px;background:var(--band-red)}
  .story{position:absolute;right:52px;top:22px;width:300px;font-family:'Roboto Condensed',sans-serif;font-style:italic;font-size:10.5px;line-height:1.45;color:var(--band-red-deep);text-align:center}
  .story p+p{margin-top:6px}
</style>
</head>
<body>
<main class="canvas">
  <section class="panel panel-lid" aria-label="Lid">
    <div class="pattern lid-pattern-left" role="img" aria-label="Grey ethnic woven border pattern"></div>
    <div class="pattern lid-pattern-right" role="img" aria-label="Grey ethnic woven border pattern"></div>
    <div class="brand brand-lid"><span class="brand-dot"></span><span>Torvel Ridge Roasters</span></div>
  </section>

  <section class="panel panel-front" aria-label="Front side">
    <div class="front-band">
      <div class="pattern front-pattern-left" role="img" aria-label="Dark ethnic woven border pattern"></div>
      <div class="pattern front-pattern-right" role="img" aria-label="Dark ethnic woven border pattern"></div>
      <div class="brand brand-front"><span class="brand-dot"></span><span>Torvel Ridge Roasters</span></div>
      <div class="story">
        <p>We are a coffee producer in the Central Highlands of Vietnam with a sustainable, fair and inclusive business model. We are producing Arabica coffee from farm to cup. We are sourcing our coffee cherries directly from local farmers which are members of an ethnic minority.</p>
        <p>Besides Arabica and Specialty Arabicas, we also produce Robusta, blends and herbal coffees with Ginseng and Ganoderma.</p>
        <p>Our products are sold to 4 and 5-star hotels, in online and retail shops in Vietnam and we will soon start to export our coffee to other countries in Asia and overseas.</p>
      </div>
    </div>
  </section>

  <section class="panel panel-end" aria-label="End side">
    <div class="brand brand-end"><span class="brand-dot"></span><span>Torvel Ridge Roasters</span></div>
  </section>
</main>
</body>
</html>
```